Der Flyer soll das Format DIN 105 lang haben und später bei druckfalter.de gedruckt werden. Entsprechende Vorlagen sind bei druckfalter.de vorhanden. Der Flyer wird in der Mitte 1x gefalzt und beidseitige bedruckt. (Es gibt also eine Außenseite, eine Doppel Innenseiten und eine Rückseite)
Der Flyer soll Neupatienten sowie BEstandspatienten ansprechen und über die Ärzte und die Leistungen informieren. Siehe www.praxis-lindenhof-beispiel.de
Die Fotos auf der Homepage können verwendet werden, entsprechende Lizenzen für die Nutzung liegen vor. An besseren Ideen bin ich natürlich auch interessiert :-)
Datenübergabe in Adobe Illustrator (.ai) oder Adobe InDesign (.indd)
Vielen Dank und beste Grüße

```html
<!DOCTYPE html>
<html lang="de">
<head>
<meta charset="utf-8">
<title>Hausarztpraxis – Leistungen</title>
<link rel="stylesheet" href="https://fonts.googleapis.com/css2?family=Caveat:wght@500&family=Montserrat:wght@400;600&display=swap">
<style>
  :root {
    --pink: #d8307f;
    --ink: #1d1d1b;
    --paper: #ffffff;
    --rule: #6f7378;
  }
  * { box-sizing: border-box; margin: 0; padding: 0; }
  html, body { width: 1200px; height: 1200px; overflow: hidden; background: var(--paper); }
  .spread {
    position: relative; width: 1200px; height: 1200px;
    border: 1px solid var(--rule);
    font-family: "Montserrat", sans-serif; color: var(--ink);
    font-size: 17.4px; line-height: 24.2px;
  }
  .fold { position: absolute; left: 599px; top: 0; width: 1.5px; height: 100%; background: var(--rule); }
  .script {
    position: absolute; font-family: "Caveat", cursive; font-weight: 500;
    color: var(--pink); font-size: 62px; line-height: 1; white-space: nowrap;
  }
  .block { position: absolute; }
  .block h3 { color: var(--pink); font-weight: 600; font-size: 17.4px; line-height: 24.2px; letter-spacing: 0.2px; }
  .block p, .block li { font-weight: 400; }
  .block ul { list-style: none; }
  .block li { padding-left: 12px; text-indent: -12px; }
  .photo { position: absolute; }
  .photo-family { left: 0; top: 467px; width: 479px; height: 357px;
    background: linear-gradient(180deg, #e9e7e3 0%, #d9c8b7 45%, #ece8e2 88%, #f5f4f2 100%); }
  .photo-doctor { left: 600px; top: 337px; width: 486px; height: 307px;
    background: linear-gradient(90deg, #e5e3e6 0%, #f1b7d0 45%, #e66aa6 75%, #f0a9c9 100%); }
  .cross { position: absolute; width: 82px; height: 82px; }
</style>
</head>
<body>
<main class="spread">
  <div class="fold"></div>

  <!-- linke Innenseite -->
  <h1 class="script" style="left:34px; top:86px;">Wie können wir helfen?</h1>

  <section class="block" style="left:34px; top:166px; width:530px;">
    <h3>Wir sind Ihr Ansprechpartner</h3>
    <p>Als Hausärzte sind wir in allen Gesundheitsfragen Ihre erste Anlaufstelle</p>
  </section>
  <section class="block" style="left:34px; top:263px; width:530px;">
    <h3>Wir sind Ihr Koordinator</h3>
    <p>Wir behalten den Überblick und leiten Untersuchungen für Sie in die Wege</p>
  </section>
  <section class="block" style="left:34px; top:360px; width:500px;">
    <h3>Wir begleiten Sie</h3>
    <p>Wir beraten Sie und unterstützen Sie dabei wieder gesund zu werden und zu bleiben</p>
  </section>

  <div class="photo photo-family" role="img" aria-label="Foto: drei Generationen einer Familie, lächelnd auf einem Sofa"></div>
  <svg class="cross" style="left:423px; top:436px;" viewBox="0 0 82 82" aria-hidden="true">
    <path d="M23 8h18v23h23v18H41v23H23V49H0V31h23z" fill="#fff" transform="translate(-4,6)"/>
    <path d="M33 6h18v26h26v18H51v26H33V50H7V32h26z" fill="var(--pink)"/>
  </svg>

  <h2 class="script" style="left:29px; top:866px;">Unsere Leistungen</h2>

  <section class="block" style="left:29px; top:937px; width:560px;">
    <h3>Diagnostische Möglichkeiten und Gesundheitsvorsorge</h3>
    <ul>
      <li>- Laboruntersuchungen</li>
      <li>- EKG (Elektrokardiogramm)</li>
      <li>- Langzeit-Blutdruckmessung (24 Stunden)</li>
      <li>- Ergometrie/ Belastungs-EKG</li>
      <li>- Sonographie / Ultraschall: Abdomen,<br>Schilddrüse, Gefäße</li>
      <li>- Spirometrie / Lungenfunktion</li>
    </ul>
  </section>

  <!-- rechte Innenseite -->
  <section class="block" style="left:635px; top:166px; width:530px;">
    <h3>Checkup und Checkup Plus</h3>
    <p>Neben der regulären Gesundheitsuntersuchung der gesetzlichen Krankenkassen bieten wir Ihnen auf Wunsch zusätzliche Selbstzahler Leistungen an, die zu Ihnen passen. Gerne beraten wir Sie individuell dazu.</p>
  </section>

  <div class="photo photo-doctor" role="img" aria-label="Foto: Ärztin in pinker Kleidung hält ein Stethoskop nach vorne"></div>
  <svg class="cross" style="left:1035px; top:306px;" viewBox="0 0 82 82" aria-hidden="true">
    <path d="M23 8h18v23h23v18H41v23H23V49H0V31h23z" fill="#fff" transform="translate(-4,6)"/>
    <path d="M33 6h18v26h26v18H51v26H33V50H7V32h26z" fill="var(--pink)"/>
  </svg>

  <section class="block" style="left:635px; top:674px; width:540px;">
    <h3>Darmkrebsvorsorge</h3>
    <p>Wir beraten zu den Möglichkeiten der Darmkrebsvorsorge und unterstützen Sie bei Ihrer Entscheidungsfindung.</p>
  </section>
  <section class="block" style="left:635px; top:771px; width:520px;">
    <h3>Hautkrebsscreening</h3>
    <p>Ab 35 Jahren können Sie alle 2 Jahre ein Hautkrebs-<br>screening in unserer Praxis durchführen lassen</p>
  </section>
  <section class="block" style="left:635px; top:868px; width:540px;">
    <h3>Screening auf Bauchaortenaneurysma</h3>
    <p>Ab dem 65. Lebensjahr haben gesetzlich versicherte Männer Anspruch auf ein Screening zur Feststellung einer Erweiterung der Bauchschlagader. Dies umfasst eine Beratung und einen Ultraschall der Bauchschlagader.</p>
  </section>
  <section class="block" style="left:635px; top:1013px; width:530px;">
    <h3>DMP (Disease Managment Program)</h3>
    <p>Wenn Sie an einer chronischen Krankheit wie Diabetes mellitus, einer Koronaren Herzkrankheit (KHK), Asthma bronchiale oder einer chronischen Bronchitis (COPD) leiden, können Sie von regelmäßigen und strukturierten Behandlungsprogrammen profitieren.</p>
  </section>
</main>
</body>
</html>
```